Dunmore Roofing

Want a professional looking business card

Industry/Entity Type

Business

Contact Information for Business Card

Paul Dunmore ( Owner) paul@dunmoreroofing-example.com, www.dunmoreroofing-example.com, Adress: 4172 Township road 43 Plantagenet,ON K9X4T2

```html
<!DOCTYPE html>
<html lang="en">
<head>
<meta charset="utf-8">
<title>Dunmore Roofing – Business Card</title>
<link rel="stylesheet" href="https://fonts.googleapis.com/css2?family=Open+Sans:wght@400;600;700;800&display=swap">
<style>
  :root {
    --canvas: #e4e5e7;
    --card-grey: #77787b;
    --brand-blue: #1c4587;
    --white: #ffffff;
    --soft-line: rgba(255,255,255,0.75);
  }
  * { box-sizing: border-box; margin: 0; padding: 0; }
  html, body {
    width: 1200px; height: 900px; overflow: hidden;
    background: var(--canvas);
    font-family: "Open Sans", Arial, sans-serif;
  }
  .stage { position: relative; width: 1200px; height: 900px; }

  .card {
    position: absolute; left: 250px; width: 700px; height: 400px;
    overflow: hidden; box-shadow: 0 6px 18px rgba(0,0,0,0.18);
  }

  /* Back side */
  .card--back { top: 40px; background: var(--card-grey); }
  .card--back .backdrop {
    position: absolute; inset: 0;
    background: radial-gradient(ellipse at 50% 45%, rgba(255,255,255,0.10), rgba(255,255,255,0) 65%);
  }
  .card--back .wordmark {
    position: absolute; top: 138px; left: 0; right: 0;
    display: flex; justify-content: center; align-items: center; gap: 14px;
    color: var(--white); font-weight: 800; font-size: 44px; letter-spacing: 2px;
    -webkit-font-smoothing: antialiased;
  }
  .wordmark .mark-square { width: 16px; height: 16px; background: currentColor; flex: none; }
  .card--back .web-row {
    position: absolute; top: 300px; left: 0; right: 0;
    display: flex; align-items: center; justify-content: center; gap: 14px;
    color: var(--white); font-size: 15px; letter-spacing: 0.5px;
  }
  .web-row .rule { width: 170px; height: 1px; background: var(--soft-line); }

  /* Front side */
  .card--front { top: 470px; background: var(--white); }
  .card--front .panel { position: absolute; inset: 0; }
  .card--front .edge-accent {
    position: absolute; left: 0; top: 140px; width: 7px; height: 200px;
    background: var(--brand-blue); border-radius: 0 4px 4px 0;
  }
  .card--front .edge-accent--light {
    position: absolute; right: 0; top: 40px; width: 7px; height: 160px;
    background: var(--white); border-radius: 4px 0 0 4px;
  }
  .card--front .wordmark {
    position: absolute; left: 40px; top: 175px; width: 290px;
    color: var(--brand-blue); font-weight: 800; font-size: 30px; letter-spacing: 1px;
    line-height: 1.35; -webkit-font-smoothing: antialiased;
  }
  .contact {
    position: absolute; left: 420px; top: 62px; width: 262px; color: var(--white);
  }
  .contact .name { font-weight: 700; font-size: 21px; }
  .contact .role { font-size: 14px; margin-top: 6px; }
  .contact .address { font-size: 14px; line-height: 1.45; margin-top: 18px; }
  .contact .lines { list-style: none; margin-top: 18px; font-size: 13.5px; line-height: 1.6; }
  .contact .lines li { display: flex; align-items: center; gap: 8px; white-space: nowrap; }
  .contact .lines svg { width: 14px; height: 14px; flex: none; }
</style>
</head>
<body>
<main class="stage">

  <section class="card card--back" aria-label="Business card back">
    <div class="backdrop" role="img" aria-label="Faint world map texture"></div>
    <div class="wordmark"><span class="mark-square"></span><span>DUNMORE ROOFING</span></div>
    <div class="web-row"><span class="rule"></span><span>www.dunmoreroofing-example.com</span><span class="rule"></span></div>
  </section>

  <section class="card card--front" aria-label="Business card front">
    <svg class="panel" viewBox="0 0 700 400" width="700" height="400" aria-hidden="true">
      <path fill="var(--brand-blue)"
        d="M300 0 H700 V400 H390 V300 Q390 280 370 280 H350 V130 Q350 110 330 110 H320 Q300 110 300 90 Z"/>
    </svg>
    <span class="edge-accent"></span>
    <span class="edge-accent--light"></span>

    <div class="wordmark">DUNMORE<br>ROOFING</div>

    <div class="contact">
      <p class="name">Paul Dunmore</p>
      <p class="role">Owner</p>
      <p class="address">4172 Township road 43,<br>Alderbrook, KN K9X4T2</p>
      <ul class="lines">
        <li><svg viewBox="0 0 16 16"><path fill="#fff" d="M4 1l3 3-2 2c1 2 3 4 5 5l2-2 3 3-2 3C7 15 1 9 1 3z"/></svg>(555) 014-7720</li>
        <li><svg viewBox="0 0 16 16"><rect x="1" y="3" width="14" height="10" rx="1" fill="#fff"/><path d="M1 4l7 5 7-5" stroke="#1c4587" stroke-width="1.3" fill="none"/></svg>paul@dunmoreroofing-example.com</li>
        <li><svg viewBox="0 0 16 16" fill="none" stroke="#fff" stroke-width="1.2"><circle cx="8" cy="8" r="6.5"/><ellipse cx="8" cy="8" rx="3" ry="6.5"/><path d="M1.5 8h13"/></svg>www.dunmoreroofing-example.com</li>
      </ul>
    </div>
  </section>

</main>
</body>
</html>
```